Social Media App Needs PPT Template

We need a PowerPoint template for a new social media company based in the DC area called "Bold Ledger." We provide an interactive digital platform for executives to share actionable advice. We would like to see designs that use our orange logo color as an accent, but are mainly grey, white, and black. The final design should communicate clean, chic, modern, and professional.

Target Market(s)

Executives

Industry/Entity Type

Information Technology

Font styles to use
Sans Serif

Colors
f78f20
fbe7d2
ffffff
000000
e8e8e8
757575

Requirements
Must have
• My project must have title page and many options for the body of the ppt (graphs, tables, etc). It also needs to be easy to modify. I must have someone who is experienced in creating powerpoint templates.
Nice to have
• It would be nice to have a very modern and clean design that includes the logo on every page, but still leaves a lot of room for the content of the slide
Should not have
• My design project should not look to busy.

```html
<!DOCTYPE html>
<html lang="en">
<head>
<meta charset="utf-8">
<title>Bold Ledger – About Our Company</title>
<link rel="stylesheet" href="https://fonts.googleapis.com/css2?family=Lato:wght@300;400;700&display=swap">
<style>
  :root {
    --orange: #f08a1c;
    --orange-deep: #e67e17;
    --navy: #222c3b;
    --grey-area: #a2a3a6;
    --slide-bg: #f3f3f3;
    --text: #555555;
    --axis: #666666;
    --stage: #545454;
    --white: #ffffff;
  }
  * { margin: 0; padding: 0; box-sizing: border-box; }
  html, body {
    width: 1200px; height: 960px; overflow: hidden;
    background: var(--stage);
    font-family: "Lato", sans-serif;
  }
  .slide {
    position: absolute; left: 0; top: 30px;
    width: 1212px; height: 910px;
    transform: scale(0.990099); transform-origin: 0 0;
    background: radial-gradient(ellipse at 50% 45%, #ffffff 0%, var(--slide-bg) 70%);
    overflow: hidden;
  }
  .slide-shapes { position: absolute; inset: 0; }
  .slide-title {
    position: absolute; left: 37px; top: 78px;
    font-weight: 300; font-size: 46px; color: var(--white);
    letter-spacing: 0.2px;
  }
  .brand {
    position: absolute; left: 982px; top: 84px;
    display: flex; align-items: center; gap: 10px;
    color: var(--white); font-weight: 700; font-size: 27px;
  }
  .brand-dot { width: 16px; height: 16px; border-radius: 50%; background: var(--orange); }
  .axis-label {
    position: absolute; width: 30px; text-align: right;
    font-size: 19px; color: var(--axis);
  }
  .category {
    position: absolute; top: 565px;
    font-size: 20px; color: var(--axis);
  }
  .legend { position: absolute; left: 1068px; top: 265px; list-style: none; }
  .legend li {
    display: flex; align-items: center; gap: 6px;
    font-size: 20px; color: var(--axis); height: 30px;
  }
  .legend .swatch { width: 11px; height: 11px; }
  .body-copy {
    position: absolute; left: 61px; top: 634px; width: 1097px;
    font-size: 21px; line-height: 30.7px; color: var(--text);
    text-align: justify;
  }
  .footer-text {
    position: absolute; left: 33px; top: 868px;
    font-size: 16.5px; color: var(--white); font-weight: 300;
  }
  .footer-text .sep { margin: 0 8px; }
</style>
</head>
<body>
  <div class="slide">
    <svg class="slide-shapes" width="1212" height="910" viewBox="0 0 1212 910" aria-hidden="true">
      <!-- header -->
      <polygon points="942,41 1212,41 1212,52 930,52" fill="var(--orange)"/>
      <polygon points="0,57 919,57 819,152 0,152" fill="var(--orange-deep)"/>
      <polygon points="730,57 919,57 850,122 650,122" fill="#f0931f" opacity="0.6"/>
      <polygon points="928,57 1212,57 1212,152 828,152" fill="var(--navy)"/>
      <polygon points="0,156 816,156 804,169 0,169" fill="var(--navy)"/>
      <!-- chart grid -->
      <g stroke="#9a9a9a" stroke-width="1" stroke-dasharray="9 7">
        <line x1="99" y1="270" x2="1032" y2="270"/>
        <line x1="99" y1="327" x2="1032" y2="327"/>
        <line x1="99" y1="381" x2="1032" y2="381"/>
        <line x1="99" y1="436" x2="1032" y2="436"/>
      </g>
      <polygon points="451,349 1032,292 1032,546 451,546" fill="var(--navy)"/>
      <polygon points="99,453 315,342 761,381 921,401 921,546 99,546" fill="var(--orange)"/>
      <polygon points="99,453 451,391 761,429 921,401 1032,381 1032,546 99,546" fill="var(--grey-area)"/>
      <g stroke="#8a8a8a" stroke-width="1">
        <line x1="99" y1="270" x2="99" y2="546"/>
        <line x1="94" y1="546" x2="1032" y2="546"/>
      </g>
      <!-- footer -->
      <polygon points="0,861 346,861 308,897 0,897" fill="var(--navy)"/>
      <polygon points="352,861 1212,861 1212,897 314,897" fill="var(--orange-deep)"/>
    </svg>

    <h1 class="slide-title">About Our Company</h1>
    <div class="brand"><span class="brand-dot"></span>Bold Ledger</div>

    <span class="axis-label" style="left:52px;top:260px">5</span>
    <span class="axis-label" style="left:52px;top:318px">4</span>
    <span class="axis-label" style="left:52px;top:371px">3</span>
    <span class="axis-label" style="left:52px;top:426px">2</span>
    <span class="axis-label" style="left:52px;top:480px">1</span>
    <span class="axis-label" style="left:52px;top:537px">0</span>

    <span class="category" style="left:98px">Category 1</span>
    <span class="category" style="left:495px">Category 2</span>
    <span class="category" style="left:912px">Category 3</span>

    <ul class="legend">
      <li><span class="swatch" style="background:var(--grey-area)"></span>Series 1</li>
      <li><span class="swatch" style="background:var(--orange)"></span>Series 2</li>
      <li><span class="swatch" style="background:var(--navy)"></span>Series 3</li>
    </ul>

    <p class="body-copy">Duis autem vel eum iriure dolor in hendrerit in vulputate velit esse molestie consequat, vel illum dolore eu feugiat nulla facilisis at vero eros et accumsan et iusto odio dignissim qui blandit praesent luptatum zzril delenit augue duis dolore te feugait nulla facilisi. Nam liber tempor cum soluta nobis eleifend option congue nihil imperdiet doming id quod mazim placerat facer possim assum.</p>

    <div class="footer-text">www.boldledger.com<span class="sep">|</span>Page 5</div>
  </div>
</body>
</html>
```